Maple Roster Business Card for recruitment company

We are looking for a Business Card Design that incorporates our personal details and our busines name and logo. We are a specialized search consultancy that recruit Property and Construction professionals.
We would like a business card that stands out and is appealing to the Construction and Property industry as well.

Target Market(s)

people in the construction and property industry

Contact Information for Business Card

Business Name and logo

Font styles to use
Serif

Colors
0094D4
00A9DD
6FCCEA
C7EBF8
E9F6FB

Requirements
Must have
• Business name and logo as well as contact details
Should not have
• No photos of us please

```html
<!DOCTYPE html>
<html lang="en">
<head>
<meta charset="utf-8">
<title>Maple Roster Business Card</title>
<link href="https://fonts.googleapis.com/css2?family=Montserrat:wght@300;400;600&display=swap" rel="stylesheet">
<style>
  :root {
    --backdrop: #d3d3d3;
    --paper: #ffffff;
    --teal: #043c4f;
    --ink: #3a3a3a;
    --white: #ffffff;
  }
  * { margin: 0; padding: 0; box-sizing: border-box; }
  html, body { width: 900px; height: 1200px; overflow: hidden; }
  body {
    background: var(--backdrop);
    font-family: "Montserrat", Arial, sans-serif;
    position: relative;
  }
  .card {
    position: absolute;
    left: 80px;
    width: 742px;
    box-shadow: 0 6px 18px rgba(0,0,0,0.35);
  }
  .card-front { top: 132px; height: 438px; background: var(--paper); border-bottom: 3px solid var(--teal); }
  .card-back { top: 638px; height: 440px; background: var(--teal); }

  .wordmark {
    position: absolute;
    left: 0; right: 0;
    text-align: center;
    font-weight: 400;
    font-size: 78px;
    letter-spacing: 3px;
    line-height: 1;
    text-transform: uppercase;
  }
  .card-front .wordmark { top: 62px; color: var(--teal); }
  .card-back .wordmark { top: 186px; color: var(--white); }

  .contact-band {
    position: absolute;
    top: 201px; left: 0;
    width: 100%; height: 144px;
    background: var(--teal);
    color: var(--white);
  }
  .person { position: absolute; right: 432px; top: 40px; text-align: right; }
  .person-name { font-size: 26px; font-weight: 600; line-height: 1; }
  .person-role { font-size: 17px; font-weight: 300; margin-top: 8px; }
  .divider {
    position: absolute; left: 352px; top: 40px;
    width: 1.5px; height: 69px; background: var(--white);
  }
  .contact-list { position: absolute; left: 386px; top: 38px; list-style: none; }
  .contact-list li {
    display: flex; align-items: center;
    font-size: 17px; font-weight: 300; height: 25px;
  }
  .contact-list svg { width: 15px; height: 15px; margin-right: 11px; fill: var(--white); }
  .address {
    position: absolute; top: 366px; left: 0; right: 0;
    text-align: center; font-size: 17px; color: var(--ink);
  }
</style>
</head>
<body>
  <section class="card card-front">
    <div class="wordmark">Maple Roster</div>
    <div class="contact-band">
      <div class="person">
        <div class="person-name">Dana Whitlock</div>
        <div class="person-role">Owner/ Designer</div>
      </div>
      <div class="divider"></div>
      <ul class="contact-list">
        <li><svg viewBox="0 0 16 16"><path d="M1 6c0-3 3-4 7-4s7 1 7 4v1h-4V5.5H5V7H1z M3 8h10l1 6H2z M8 9.5a2 2 0 1 0 0 4a2 2 0 1 0 0-4z"/></svg>(555) 214-0387</li>
        <li><svg viewBox="0 0 16 16"><path d="M1 4h14v1l-7 4.5L1 5z M1 6.5l7 4.5 7-4.5V13H1z"/></svg>info@mapleroster.com</li>
        <li><svg viewBox="0 0 16 16"><circle cx="8" cy="8" r="7"/><path d="M4 5h3v3H5z M9 9h3l-1 3H9z" fill="#043c4f"/></svg>www.mapleroster.com</li>
      </ul>
    </div>
    <div class="address">82 Harbor Lane, Linden Bay, CA 94017</div>
  </section>

  <section class="card card-back">
    <div class="wordmark">Maple Roster</div>
  </section>
</body>
</html>
```